Graphics for Verdaxa telehealth weight loss plans

Verdaxa focuses on delivering medical weight-loss using prescription medicine and telehealth consults. Verdaxa needs graphics for its ecommerce site for three weight loss plans. The plans are posted here with current graphics and descriptions of what is included with each plan. Please do not feel constrained by current graphics or styling.

- https://store.verdaxahealth.com/products/radiant-horizon-plan
- https://store.verdaxahealth.com/products/medication-kickstart-plan
- https://store.verdaxahealth.com/products/balanced-ascent-plan

The graphics need to look good on mobile and desktop browsers.

```html
<!DOCTYPE html>
<html lang="en">
<head>
<meta charset="utf-8">
<title>Verdaxa Weight Loss Plans</title>
<link href="https://fonts.googleapis.com/css2?family=Oswald:wght@300;400;500;600;700&display=swap" rel="stylesheet">
<style>
  :root {
    --cyan: #14c0ef;
    --indigo: #2a2461;
    --royal: #1f4fa8;
    --white: #ffffff;
  }
  * { box-sizing: border-box; margin: 0; padding: 0; }
  html, body { width: 1200px; height: 520px; overflow: hidden; background: var(--white); }
  body { font-family: "Oswald", sans-serif; position: relative; }

  .plan-card {
    position: absolute; top: 14px; width: 380px; height: 492px; overflow: hidden;
  }
  .plan-card--kickstart { left: 19px; background: var(--cyan); color: var(--indigo); }
  .plan-card--ascent { left: 410px; background: var(--indigo); color: var(--cyan); }
  .plan-card--horizon { left: 801px; background: var(--royal); color: var(--white); }

  .plan-photo {
    position: absolute; top: 0; left: 0; width: 100%; height: 157px;
    clip-path: polygon(0 0, 100% 0, 100% 100%, 77% 100%, 77% 69%, 0 69%);
  }
  .plan-photo--scale { background: linear-gradient(110deg, #bdbdbd 0%, #e3e3e3 45%, #9a9a9a 75%, #d6d6d6 100%); }
  .plan-photo--shake { background: linear-gradient(100deg, #8a8a8a 0%, #c9c9c9 40%, #b0b0b0 70%, #5c5c5c 100%); }
  .plan-photo--core { background: linear-gradient(100deg, #4a4a4a 0%, #9c9c9c 30%, #d4d4d4 65%, #aaaaaa 100%); }

  .plan-body { position: absolute; left: 26px; right: 10px; top: 112px; }

  .plan-title {
    font-weight: 700; font-size: 42px; line-height: 42px; letter-spacing: 0.3px;
    text-transform: uppercase;
  }
  .plan-card--horizon .plan-title { font-size: 38px; line-height: 43px; margin-top: 2px; }
  .plan-subtitle {
    font-weight: 400; font-size: 20px; line-height: 23px; margin-top: 4px;
    text-transform: uppercase;
  }
  .includes-tag {
    display: inline-block; font-weight: 500; font-size: 14px; line-height: 20px;
    padding: 0 8px; border-radius: 2px; margin-top: 9px;
  }
  .plan-card--kickstart .includes-tag { background: var(--indigo); color: var(--white); }
  .plan-card--ascent .includes-tag { background: var(--cyan); color: var(--indigo); }
  .plan-card--horizon .includes-tag { background: var(--white); color: var(--indigo); }

  .feature-columns { display: flex; margin-top: 9px; margin-left: -3px; }
  .feature-columns .feature-list:first-child { width: 150px; }
  .feature-columns .feature-list:last-child { width: 190px; }

  .feature-list { list-style: none; display: flex; flex-direction: column; }
  .feature-list--left { row-gap: 7px; }
  .feature-list--right { row-gap: 12px; margin-top: -3px; }
  .feature-list--single { row-gap: 12px; margin-top: 10px; margin-left: -3px; }

  .feature-grid {
    list-style: none; margin-top: 10px; margin-left: -4px;
    display: grid; grid-template-columns: 160px 1fr; column-gap: 2px; row-gap: 9px;
  }

  .feature-list li, .feature-grid li {
    position: relative; padding-left: 9px; font-weight: 500; font-size: 15px; line-height: 17px;
    letter-spacing: -0.1px;
  }
  .feature-list li::before, .feature-grid li::before { content: "•"; position: absolute; left: 0; top: 0; }
  .feature-note { display: block; font-weight: 400; font-size: 11px; line-height: 14px; }
  .feature-note--inline { display: inline; margin-left: 4px; }
  .feature-qty { font-weight: 400; font-size: 11px; }

  .plan-disclaimer { font-weight: 300; font-size: 12px; margin-top: 11px; padding-left: 0; }

  .billing-tag {
    position: absolute; left: 23px; top: 431px;
    font-weight: 500; font-size: 13.5px; line-height: 21px; padding: 0 10px; border-radius: 2px;
  }
  .plan-card--kickstart .billing-tag { background: var(--indigo); color: var(--white); }
  .plan-card--ascent .billing-tag { background: var(--cyan); color: var(--white); }
  .plan-card--horizon .billing-tag { background: var(--white); color: var(--royal); }
</style>
</head>
<body>

<section class="plan-card plan-card--kickstart">
  <div class="plan-photo plan-photo--scale" role="img" aria-label="Photo of a tape measure around a waist beside scattered capsules"></div>
  <div class="plan-body">
    <h2 class="plan-title">Medication<br>Kickstart Plan</h2>
    <p class="plan-subtitle">Physician Consultation<br>Phentermine Program</p>
    <span class="includes-tag">Includes</span>
    <div class="feature-columns">
      <ul class="feature-list feature-list--left">
        <li>100% online.<span class="feature-note">No need to visit the office.</span></li>
        <li>Phentermine<br>prescription.</li>
        <li>Medical<br>consultation.</li>
      </ul>
      <ul class="feature-list feature-list--right">
        <li>Real Phentermine <span class="feature-qty">(37.5mg/Pill)</span><br>delivered to your door.</li>
        <li>1 month supply. <span class="feature-qty">(30 pills)</span></li>
        <li>FREE Introductory Nutritionist<br>consult on your first month.</li>
      </ul>
    </div>
  </div>
  <span class="billing-tag">Month-to-month pay as you go.</span>
</section>

<section class="plan-card plan-card--ascent">
  <div class="plan-photo plan-photo--shake" role="img" aria-label="Photo of a woman in sportswear holding a protein shaker"></div>
  <div class="plan-body">
    <h2 class="plan-title">Balanced<br>Ascent Plan</h2>
    <span class="includes-tag">Includes</span>
    <ul class="feature-list feature-list--single">
      <li>100% online.<span class="feature-note feature-note--inline">No need to visit the office.</span></li>
      <li>Expert nutrition consult.</li>
      <li>Custom crafted diet plan to achieve your goals.</li>
      <li>Nutrition coaching to improve your health and vitality.</li>
    </ul>
    <p class="plan-disclaimer">*Does not include medication</p>
  </div>
  <span class="billing-tag">Month-to-month pay as you go.</span>
</section>

<section class="plan-card plan-card--horizon">
  <div class="plan-photo plan-photo--core" role="img" aria-label="Photo of a toned midriff beside scattered capsules"></div>
  <div class="plan-body">
    <h2 class="plan-title">Radiant<br>Horizon Plan</h2>
    <p class="plan-subtitle">Physician Consultation<br>Phentermine Program</p>
    <span class="includes-tag">Includes</span>
    <ul class="feature-grid">
      <li>100% online.<span class="feature-note">No need to visit the office.</span></li>
      <li>Real Phentermine <span class="feature-qty">(37.5mg/Pill)</span><br>delivered to your door.</li>
      <li>1 month supply. <span class="feature-qty">(30 pills)</span></li>
      <li>Expert nutrition consult.</li>
      <li>Custom crafted diet plan<br>to achieve your goals.</li>
      <li>Nutrition coaching to improve<br>your health and vitality.</li>
    </ul>
  </div>
  <span class="billing-tag">Month-to-month pay as you go.</span>
</section>

</body>
</html>
```